Boutique Technology Consultancy specialising is Electronic and physical security

We need to redo our existing outdated website. For your reference the link www.pelu.com.au

```html
<!DOCTYPE html>
<html lang="en">
<head>
<meta charset="utf-8">
<title>Pelu Services</title>
<link href="https://fonts.googleapis.com/css2?family=Roboto:wght@300;400;500;700&display=swap" rel="stylesheet">
<style>
:root{
  --bg:#121212;
  --bg-deep:#0b0b0b;
  --panel:#161616;
  --red:#e0262a;
  --red-dark:#a8161a;
  --white:#ffffff;
  --text:#d9d9d9;
  --muted:#9a9a9a;
  --line:#4a4a4a;
}
*{margin:0;padding:0;box-sizing:border-box}
html,body{width:1200px;height:3794px;overflow:hidden}
body{background:var(--bg);color:var(--text);font-family:'Roboto',sans-serif;position:relative}

/* header */
.site-header{position:absolute;left:0;top:0;width:1200px;height:70px;background:var(--bg-deep);z-index:5}
.brand{position:absolute;display:flex;align-items:center;gap:10px;color:var(--white);font-weight:700;letter-spacing:1px}
.brand .mark{width:16px;height:16px;background:var(--red)}
.site-header .brand{left:147px;top:18px;font-size:26px}
.main-nav{position:absolute;left:393px;top:24px;display:flex;gap:36px}
.main-nav a{color:var(--white);text-decoration:none;font-size:14px;font-weight:500;position:relative}
.main-nav a.active::after{content:"";position:absolute;left:0;right:0;bottom:-10px;height:3px;background:var(--red)}
.login-btn{position:absolute;left:958px;top:18px;width:96px;height:31px;background:var(--red);color:var(--white);font-size:14px;font-weight:500;display:flex;align-items:center;justify-content:center;gap:6px}

/* hero */
.hero{position:absolute;left:0;top:70px;width:1200px;height:560px;overflow:hidden}
.hero-visual{position:absolute;inset:0;background:radial-gradient(ellipse at 25% 45%,#6b1a1e 0%,#2a0f16 30%,transparent 55%),radial-gradient(ellipse at 80% 35%,#33526e 0%,#162536 35%,transparent 60%),linear-gradient(180deg,#0f1a27,#0c0f16)}
.hero-text{position:absolute;left:0;width:1200px;text-align:center;color:var(--white)}
.hero .kicker{top:130px;color:var(--red);font-size:12px;font-weight:700}
.hero h1{top:162px;font-size:42px;font-weight:700;letter-spacing:0.5px}
.hero h1 span{font-weight:300}
.hero .tagline{top:229px;font-size:15px}
.btn{position:absolute;display:flex;height:41px;color:var(--white);font-size:14px;font-weight:700}
.btn .label{background:var(--red);display:flex;align-items:center;justify-content:center;flex:1;text-transform:uppercase}
.btn .arrow{width:40px;background:var(--red-dark);display:flex;align-items:center;justify-content:center}
.hero-chevron{position:absolute;left:0;top:520px;width:1200px;height:110px}

/* section titles */
.section-title{position:absolute;left:0;width:1200px;display:flex;align-items:center;justify-content:center;gap:16px;font-size:36px;color:var(--white);font-weight:700}
.section-title::before,.section-title::after{content:"";width:73px;height:2px;background:var(--line)}
.section-title .accent{color:var(--red);font-weight:400}

/* about */
.about-visual{position:absolute;left:147px;top:680px;width:370px;height:405px;background:radial-gradient(ellipse at 55% 45%,#5a2224 0%,#2a1416 55%,var(--bg) 80%)}
.about-title{position:absolute;left:598px;top:690px;width:456px;display:flex;align-items:center;justify-content:center;gap:16px;font-size:36px;font-weight:700;color:var(--white)}
.about-title::before,.about-title::after{content:"";width:70px;height:2px;background:var(--line)}
.about-title .accent{color:var(--red);font-weight:400}
.about-copy{position:absolute;left:598px;top:756px;width:456px;font-size:12.5px;line-height:24px;text-align:justify;color:var(--text)}
.about-copy p{margin-bottom:10px}
.tick-list{list-style:none}
.tick-list li{position:relative;padding-left:18px;font-size:12.5px;line-height:29px;color:var(--text)}
.tick-list li::before{content:"";position:absolute;left:0;top:50%;width:12px;height:12px;margin-top:-6px;border-radius:50%;background:var(--red)}
.tick-list li::after{content:"";position:absolute;left:4px;top:50%;width:3px;height:6px;margin-top:-4px;border:solid var(--white);border-width:0 1.5px 1.5px 0;transform:rotate(45deg)}

/* experience */
.exp-intro{position:absolute;left:150px;top:1222px;width:900px;text-align:center;font-size:17px;line-height:27px;color:var(--text)}
.exp-track{position:absolute;left:0;top:1326px;width:1200px;height:280px;display:flex}
.exp-card{position:relative;width:300px;height:280px;overflow:hidden}
.exp-card .photo{position:absolute;inset:0}
.exp-card h3{position:absolute;left:0;right:0;top:24px;text-align:center;color:var(--white);font-size:16px;font-weight:500}
.exp-card .side{position:absolute;left:8px;bottom:110px;transform:rotate(-90deg);transform-origin:left bottom;font-size:9px;color:var(--white);letter-spacing:0.5px;white-space:nowrap}
.exp-card.open{width:304px;border:1px solid #ff8f8f}
.exp-card.open .overlay{position:absolute;inset:0;background:rgba(224,38,42,0.82)}
.exp-card.open h3{top:38px}
.exp-card.open p{position:absolute;left:22px;right:22px;top:78px;text-align:center;font-size:12.5px;line-height:23px;color:var(--white)}
.exp-card.open .zoom{position:absolute;left:124px;top:185px;width:56px;height:56px;border-radius:50%;background:#5b1316;display:flex;align-items:center;justify-content:center}
.dots{position:absolute;left:562px;top:1644px;display:flex;gap:4px}
.dots span{width:12px;height:12px;border-radius:50%;border:1.5px solid var(--white)}
.dots span.on{background:var(--red);border-color:var(--red)}

/* services */
.service-card{position:absolute;top:1806px;width:289px;height:365px;border:1px solid #2e2e2e;background:var(--panel)}
.service-card .photo{position:absolute;left:0;top:0;width:100%;height:214px}
.service-card .icon{position:absolute;left:112px;top:157px;width:64px;height:64px;border-radius:50%;background:var(--red);border:3px solid #5c1214;display:flex;align-items:center;justify-content:center}
.service-card h3{position:absolute;left:0;right:0;top:234px;text-align:center;color:var(--white);font-size:17px;font-weight:700}
.service-card .tick-list{position:absolute;left:64px;top:266px}
.service-card .tick-list li{line-height:24.5px;font-size:13px}
.carousel-arrow{position:absolute;top:1974px}

/* team */
.member{position:absolute;top:2370px;width:209px;text-align:center}
.member .photo{width:209px;height:268px;position:relative}
.member .plate{position:absolute;left:0;right:0;bottom:0;height:59px;background:rgba(40,40,40,0.75);color:var(--white)}
.member .plate strong{display:block;font-size:15px;margin-top:10px}
.member .plate small{display:block;font-size:10px;margin-top:2px}
.member p{font-size:13px;line-height:22px;margin-top:10px;color:var(--text)}
.socials{display:flex;justify-content:center;gap:10px;margin-top:14px}
.socials span{width:22px;height:22px;border-radius:50%;background:var(--red)}

/* contact */
.contact-info{position:absolute;top:2968px;display:flex;gap:12px;align-items:flex-start}
.contact-info h4{color:var(--white);font-size:15px;font-weight:700}
.contact-info p{color:var(--text);font-size:13px;margin-top:3px}
.field{position:absolute;border:1px solid #3a3a3a;background:rgba(18,18,18,0.7);color:var(--text);font-size:12.5px;padding:16px 19px;border-radius:3px}
.contact-bg{position:absolute;left:0;top:3180px;width:1200px;height:220px;background:radial-gradient(ellipse at 50% 60%,#202226 0%,transparent 65%)}

/* footer */
.footer-band{position:absolute;left:0;top:3395px;width:1200px;height:100px}
.site-footer{position:absolute;left:0;top:3490px;width:1200px;height:304px;background:var(--bg-deep)}
.site-footer .brand{left:144px;top:48px;font-size:46px}
.footer-socials{position:absolute;left:194px;top:143px;display:flex;gap:9px}
.footer-socials span{width:24px;height:24px;border-radius:50%;border:1.5px solid var(--white)}
.footer-col{position:absolute;top:25px}
.footer-col h4{color:var(--white);font-size:14px;font-weight:700;margin-bottom:14px}
.footer-col li{list-style:none;font-size:12.5px;line-height:24px;color:var(--text)}
.footer-contact .item{position:relative;padding-left:30px;margin-bottom:6px}
.footer-contact .item b{display:block;color:var(--white);font-size:11.5px;font-weight:700;line-height:20px}
.footer-contact .item span{font-size:12.5px;color:var(--text);line-height:22px}
.footer-contact svg{position:absolute;left:6px;top:4px}
.copyright{position:absolute;left:0;top:248px;width:1200px;text-align:center;font-size:13px;color:var(--text)}
.to-top{position:absolute;left:1078px;top:218px;width:32px;height:32px;border-radius:50%;background:var(--red);display:flex;align-items:center;justify-content:center}
</style>
</head>
<body>

<header class="site-header">
  <div class="brand"><span class="mark"></span>PELU SERVICES</div>
  <nav class="main-nav">
    <a class="active">Welcome</a><a>Experience</a><a>Services</a><a>Team</a><a>About</a><a>Contact</a>
  </nav>
  <div class="login-btn">Login
    <svg width="10" height="11" viewBox="0 0 10 11"><rect x="1" y="5" width="8" height="6" fill="#fff"/><path d="M3 5V3.5a2 2 0 0 1 4 0V5" stroke="#fff" fill="none" stroke-width="1.4"/></svg>
  </div>
</header>

<section class="hero">
  <div class="hero-visual" role="img" aria-label="Glowing robotic hand reaching toward a human hand on a dark tech background"></div>
  <div class="hero-text kicker">WELCOME TO</div>
  <h1 class="hero-text">PELU <span>SERVICES</span></h1>
  <div class="hero-text tagline">Your Technology Projects Made Easy.</div>
  <div class="btn" style="left:514px;top:285px;width:172px"><span class="label">Get Started</span><span class="arrow"><svg width="18" height="12" viewBox="0 0 18 12"><path d="M0 6h16M11 1l5 5-5 5" stroke="#fff" fill="none" stroke-width="1.6"/></svg></span></div>
</section>
<svg class="hero-chevron" viewBox="0 0 1200 110" preserveAspectRatio="none">
  <polygon points="0,10 600,80 1200,10 1200,110 0,110" fill="var(--bg)"/>
  <polygon points="0,12 600,70 1200,12 1200,16 600,92 0,16" fill="var(--red)"/>
</svg>

<!-- about -->
<div class="about-visual" role="img" aria-label="Decorative brand graphic framing a photo of a team at work"></div>
<h2 class="about-title">ABOUT <span class="accent">US</span></h2>
<div class="about-copy">
  <p>In 2022, Pelu Services merged Norvane Group into its operations, bringing increased capacity and capability to the NSW office.</p>
  <p>Pelu is a privately owned independent consultancy 100% dedicated to customer satisfaction. With experience in a range of technologies such as internet of things, security systems, wi-fi, building services networks, control centres and smart buildings, our services.</p>
  <ul class="tick-list">
    <li>Discounts for non-profit and community organisations.</li>
    <li>Engaging suppliers with inclusive employment practices.</li>
    <li>Paying Australian small businesses on time.</li>
  </ul>
</div>
<div class="btn" style="left:599px;top:1029px;width:174px;height:38px;font-size:13px"><span class="label">Learn More</span><span class="arrow"><svg width="16" height="12" viewBox="0 0 16 12"><path d="M0 6h14M9 1l5 5-5 5" stroke="#fff" fill="none" stroke-width="1.6"/></svg></span></div>

<!-- experience -->
<h2 class="section-title" style="top:1158px"><span class="accent">OUR</span>EXPERIENCE</h2>
<p class="exp-intro">Pelu has a diverse range of project experience across a range of industries within both the public and private sectors. The following is a small sample of some of the clients and sites we have worked with.</p>
<div class="exp-track">
  <div class="exp-card"><div class="photo" role="img" aria-label="Glass dome over a historic brick tower" style="background:linear-gradient(160deg,#5a6470,#2a2f36 60%,#7a4a34)"></div><h3>Harbour Arcade</h3><span class="side">CLICK HERE</span></div>
  <div class="exp-card"><div class="photo" role="img" aria-label="Aerial view of a motorway interchange through greenery" style="background:linear-gradient(170deg,#7d8a86,#56624c 50%,#3f4a3a)"></div><h3>Ridgeway Link</h3><span class="side">CLICK HERE</span></div>
  <div class="exp-card open"><div class="photo" role="img" aria-label="Hospital ward interior" style="background:linear-gradient(160deg,#b9b4b0,#8a8580)"></div><div class="overlay"></div><h3>Southgate Care Hospital</h3><p>Security technology lifecycle consulting for this leading Health Care Public Private Partnership (PPP) which is operated by Brenton &amp; Hale.</p><div class="zoom"><svg width="24" height="24" viewBox="0 0 24 24"><circle cx="10" cy="10" r="7" stroke="#fff" stroke-width="2" fill="none"/><path d="M15 15l6 6M10 7v6M7 10h6" stroke="#fff" stroke-width="2"/></svg></div></div>
  <div class="exp-card"><div class="photo" role="img" aria-label="Bank building facade with large sign" style="background:linear-gradient(170deg,#6c7888,#3c4654 55%,#262d36)"></div><h3>Coastal Mutual Bank</h3><span class="side">CLICK HERE</span></div>
</div>
<div class="dots"><span></span><span></span><span class="on"></span><span></span><span></span></div>

<!-- services -->
<h2 class="section-title" style="top:1716px"><span class="accent">OUR</span>SERVICES</h2>
<svg class="carousel-arrow" style="left:48px" width="22" height="32" viewBox="0 0 22 32"><path d="M18 2L4 16l14 14" stroke="#777" stroke-width="3" fill="none"/></svg>
<svg class="carousel-arrow" style="left:1102px" width="22" height="32" viewBox="0 0 22 32"><path d="M4 2l14 14L4 30" stroke="#777" stroke-width="3" fill="none"/></svg>

<div class="service-card" style="left:144px">
  <div class="photo" role="img" aria-label="Consultant presenting to a team in a meeting room" style="background:linear-gradient(170deg,#d6d6d4,#9a9896 60%,#5c5650)"></div>
  <div class="icon"><svg width="30" height="30" viewBox="0 0 30 30"><circle cx="15" cy="15" r="12" stroke="#fff" stroke-width="1.8" fill="none"/><circle cx="15" cy="15" r="7" stroke="#fff" stroke-width="1.8" fill="none"/><circle cx="15" cy="15" r="2" fill="#fff"/></svg></div>
  <h3>STRATEGY</h3>
  <ul class="tick-list"><li>Technology roadmaps</li><li>Master standards</li><li>Asset management</li></ul>
</div>
<div class="service-card" style="left:456px">
  <div class="photo" role="img" aria-label="Team gathered around a table reviewing plans" style="background:linear-gradient(170deg,#8a8a8a,#4a4644 60%,#2c2a28)"></div>
  <div class="icon"><svg width="26" height="30" viewBox="0 0 26 30"><rect x="3" y="4" width="20" height="24" rx="2" stroke="#fff" stroke-width="1.8" fill="none"/><path d="M8 12h10M8 17h10M8 22h6" stroke="#fff" stroke-width="1.8"/></svg></div>
  <h3>PROJECTS</h3>
  <ul class="tick-list"><li>Procurement</li><li>Technical project management</li><li>Witness testingplans</li></ul>
</div>
<div class="service-card" style="left:767px">
  <div class="photo" role="img" aria-label="Two colleagues working together on a laptop" style="background:linear-gradient(170deg,#b9aea2,#7c6a5a 60%,#4a3c30)"></div>
  <div class="icon"><svg width="26" height="30" viewBox="0 0 26 30"><rect x="3" y="4" width="20" height="24" rx="2" stroke="#fff" stroke-width="1.8" fill="none"/><path d="M8 11h10M8 16h10M8 21h10" stroke="#fff" stroke-width="1.8"/></svg></div>
  <h3>OPERATIONS &amp; MAINTENANCE</h3>
  <ul class="tick-list"><li>Policies and procedures</li><li>Procurement</li><li>Service reviews plans</li></ul>
</div>

<!-- team -->
<h2 class="section-title" style="top:2280px">OUR <span class="accent">TEAM</span></h2>
<div class="member" style="left:143px">
  <div class="photo" role="img" aria-label="Portrait of the principal consultant" style="background:linear-gradient(180deg,#bfc3c6,#8a8e92)"><div class="plate"><strong>Tom Mercer</strong><small>Principal Consultant</small></div></div>
  <p>Tom founded Pelu in 2016 and continues to lead the organisation nationally.</p>
  <div class="socials"><span></span><span></span><span></span><span></span></div>
</div>
<div class="member" style="left:378px">
  <div class="photo" role="img" aria-label="Portrait of the senior consultant" style="background:linear-gradient(180deg,#5a5a5a,#2e2e2e)"><div class="plate"><strong>Paul Hendry</strong><small>Senior Consultant</small></div></div>
  <p>Paul established Pelu's Queensland office in 2019 and leads all of Pelu's.</p>
  <div class="socials"><span></span><span></span><span></span><span></span></div>
</div>
<div class="member" style="left:612px">
  <div class="photo" role="img" aria-label="Portrait of a consultant" style="background:linear-gradient(180deg,#7a736c,#4c4640)"><div class="plate"><strong>Mark Vellani</strong><small>Consultant</small></div></div>
  <p>Mark joined Pelu in 2021, bringing a wealth of industry knowledge and experience.</p>
  <div class="socials"><span></span><span></span><span></span><span></span></div>
</div>
<div class="member" style="left:846px">
  <div class="photo" role="img" aria-label="Portrait of the administration coordinator" style="background:linear-gradient(180deg,#eceae8,#c9c4c0)"><div class="plate"><strong>Lena Hartono</strong><small>Administration Coordinator</small></div></div>
  <p>Lena founded Pelu in 2016 and continues to lead the organisation nationally.</p>
  <div class="socials"><span></span><span></span><span></span><span></span></div>
</div>

<!-- contact -->
<div class="contact-bg"></div>
<h2 class="section-title" style="top:2898px">CONTACT <span class="accent">US</span></h2>
<div class="contact-info" style="left:210px">
  <svg width="36" height="38" viewBox="0 0 36 38"><path d="M18 3a9 9 0 0 0-9 9c0 7 9 16 9 16s9-9 9-16a9 9 0 0 0-9-9z" stroke="var(--red)" stroke-width="2" fill="none"/><circle cx="18" cy="12" r="3.5" stroke="var(--red)" stroke-width="2" fill="none"/><ellipse cx="18" cy="32" rx="15" ry="4" stroke="var(--red)" stroke-width="2" fill="none"/></svg>
  <div><h4>ADDRESS</h4><p>PO Box 4120 Melbourne Vic 3000</p></div>
</div>
<div class="contact-info" style="left:526px">
  <svg width="38" height="38" viewBox="0 0 38 38"><path d="M8 4l6 0 3 8-4 3c2 5 5 8 10 10l3-4 8 3v6c0 2-2 4-4 4C16 34 4 22 4 8c0-2 2-4 4-4z" stroke="var(--red)" stroke-width="2" fill="none"/></svg>
  <div><h4>PHONE NUMBER</h4><p>1300 555 014</p></div>
</div>
<div class="contact-info" style="left:757px">
  <svg width="40" height="34" viewBox="0 0 40 34"><rect x="2" y="4" width="36" height="26" stroke="var(--red)" stroke-width="2" fill="none"/><path d="M2 4l18 15L38 4M2 30l13-13M38 30L25 17" stroke="var(--red)" stroke-width="2" fill="none"/></svg>
  <div><h4>EMAIL</h4><p>hello@pelu.com.au</p></div>
</div>
<div class="field" style="left:185px;top:3062px;width:404px;height:48px">Name</div>
<div class="field" style="left:185px;top:3124px;width:404px;height:48px">Email Address</div>
<div class="field" style="left:185px;top:3184px;width:404px;height:49px">Phone Number</div>
<div class="field" style="left:609px;top:3062px;width:407px;height:172px">Message</div>
<div class="btn" style="left:514px;top:3275px;width:173px;height:39px;font-size:13px"><span class="label">Submit Now</span><span class="arrow"><svg width="16" height="12" viewBox="0 0 16 12"><path d="M0 6h14M9 1l5 5-5 5" stroke="#fff" fill="none" stroke-width="1.6"/></svg></span></div>

<!-- footer -->
<svg class="footer-band" viewBox="0 0 1200 100" preserveAspectRatio="none">
  <polygon points="0,95 600,3 1200,95 1200,100 0,100" fill="var(--bg-deep)"/>
  <polygon points="0,92 600,0 1200,92 1200,96 600,22 0,96" fill="var(--red)"/>
</svg>
<footer class="site-footer">
  <div class="brand"><span class="mark" style="width:26px;height:26px"></span>PELU</div>
  <div class="footer-socials"><span></span><span></span><span></span><span></span></div>
  <div class="footer-col" style="left:442px"><h4>QUICK LINKS</h4><ul><li>Home</li><li>About</li><li>Services</li><li>Our Team</li><li>Experience</li><li>Contact Us</li></ul></div>
  <div class="footer-col" style="left:620px"><h4>ABOUT COMPANY</h4><ul><li>Site Map</li><li>Support</li><li>Terms &amp; Condition</li><li>Privacy Policy</li><li>FAQ</li></ul></div>
  <div class="footer-col footer-contact" style="left:835px"><h4>CONTACT US</h4>
    <div class="item"><svg width="12" height="12" viewBox="0 0 12 12"><path d="M2 1h3l1 3-2 1c1 2 2 3 4 4l1-2 3 1v3c0 1-1 1-1 1C5 12 0 7 1 2c0-1 1-1 1-1z" fill="var(--red)"/></svg><b>Phone</b><span>1300 555 014</span></div>
    <div class="item"><svg width="13" height="10" viewBox="0 0 13 10"><rect width="13" height="10" fill="var(--red)"/><path d="M0 0l6.5 5L13 0" stroke="#0b0b0b" fill="none"/></svg><b>Email</b><span>hello@pelu.com.au</span></div>
    <div class="item"><svg width="10" height="13" viewBox="0 0 10 13"><path d="M5 0a5 5 0 0 0-5 5c0 4 5 8 5 8s5-4 5-8a5 5 0 0 0-5-5z" fill="var(--red)"/><circle cx="5" cy="5" r="1.8" fill="#0b0b0b"/></svg><b>Location</b><span>PO Box 4120 Melbourne Vic 3000</span></div>
  </div>
  <div class="to-top"><svg width="14" height="10" viewBox="0 0 14 10"><path d="M1 8l6-6 6 6" stroke="#fff" stroke-width="2" fill="none"/></svg></div>
  <p class="copyright">2023 Copyright - &nbsp;Pelu Services Pty Ltd &nbsp;| All Rights Reserved</p>
</footer>

</body>
</html>
```